Business Card Design Project

I require a business card with the following information on them for various different people;
name
m:
f:
e:
I have a logo already and will attached that. We are in the construction industry. I require something clean and simple but eye catching at the same time. You can use another colour with our logo if you like and you can style the logo as well if you wish. I am open.
Also it needs to be front and back design.
Industry/Entity Type
Construction
Requirements
Must have
- Logo, name, mobile, fax and email address.
Front and back design

```html
<!DOCTYPE html>
<html lang="en">
<head>
<meta charset="utf-8">
<title>Harbor Ridge Builders – Business Card</title>
<link href="https://fonts.googleapis.com/css2?family=Open+Sans:wght@400;600;700&display=swap" rel="stylesheet">
<style>
  :root {
    --backdrop: #ebe6df;
    --card: #ffffff;
    --brand-green: #5aae3c;
    --band-dark: #4a8a2a;
    --band-light: #bcd85a;
    --ink: #4a4a4a;
    --ink-soft: #5c5c5c;
    --rule: #3d3d3d;
  }
  * { box-sizing: border-box; margin: 0; padding: 0; }
  html, body {
    width: 1200px;
    height: 407px;
    overflow: hidden;
    background: var(--backdrop);
    font-family: "Open Sans", Arial, sans-serif;
  }
  .card {
    position: absolute;
    top: 60px;
    width: 505px;
    height: 288px;
    background: var(--card);
    box-shadow: 0 3px 10px rgba(0, 0, 0, 0.25);
    overflow: hidden;
  }
  .card-front { left: 56px; }
  .card-back { left: 638px; }

  .brand {
    position: absolute;
    left: 0;
    right: 0;
    display: flex;
    align-items: center;
    justify-content: center;
    gap: 12px;
    color: var(--brand-green);
    font-weight: 600;
    letter-spacing: 0.5px;
    line-height: 1.2;
  }
  .brand-square {
    width: 22px;
    height: 22px;
    background: var(--brand-green);
    border-radius: 3px;
    flex: none;
  }
  .card-front .brand { top: 56px; font-size: 36px; }
  .card-back .brand { top: 124px; font-size: 30px; }
  .card-back .brand-square { width: 26px; height: 26px; }

  .holder {
    position: absolute;
    top: 172px;
    left: 0;
    right: 0;
    text-align: center;
    color: var(--ink);
    line-height: 22px;
  }
  .holder-name { font-size: 16px; font-weight: 700; }
  .holder-title { font-size: 12.5px; font-weight: 400; color: var(--ink-soft); }

  .contact-line {
    position: absolute;
    top: 222px;
    left: 0;
    right: 0;
    text-align: center;
    font-size: 12.5px;
    line-height: 18px;
    color: var(--ink);
  }
  .contact-line span + span { margin-left: 12px; }

  .rule {
    position: absolute;
    top: 246px;
    left: 0;
    right: 0;
    height: 2px;
    background: var(--rule);
  }
  .footer-band {
    position: absolute;
    left: 0;
    right: 0;
    bottom: 0;
    height: 35px;
    background: linear-gradient(90deg, var(--band-dark) 0%, #7fb042 25%, var(--band-light) 52%, #7fb042 78%, var(--band-dark) 100%);
    display: flex;
    align-items: center;
    justify-content: center;
    font-size: 12.5px;
    color: #2f3a22;
  }
</style>
</head>
<body>
  <section class="card card-front">
    <div class="brand"><span class="brand-square"></span>Harbor Ridge Builders</div>
    <div class="holder">
      <span class="holder-name">Your Name</span>
      <span class="holder-title"> / Title</span>
    </div>
    <div class="contact-line">
      <span>C : 123-456-7890</span>
      <span>F : 123-456-7890</span>
      <span>E : name@website.com</span>
    </div>
    <div class="rule"></div>
    <div class="footer-band">www.website.com</div>
  </section>

  <section class="card card-back">
    <div class="brand"><span class="brand-square"></span>Harbor Ridge Builders</div>
  </section>
</body>
</html>
```